MEDICAL CLINIC LETTERHEAD

Design is a letterhead for a non-profit medical center. The name of the clinic is VITARIDGE Community Health Center. Although the full name must be included, the community health center part is more of a description and should be less visible - i attached an example of what I mean by that (ATTACHED IMAGE IS AN EXAMPLE OF FONT SIZES NOT A DESIGN IDEA). Please design something modern, cool looking and unique because I can always download free templates.
Phone, email, website and etc will be added later.

Industry/Entity Type

MEDICAL

```html
<!DOCTYPE html>
<html lang="en">
<head>
<meta charset="utf-8">
<title>VITARIDGE Community Health Center – Letterhead</title>
<link rel="stylesheet" href="https://fonts.googleapis.com/css2?family=Montserrat:wght@600;700&family=Questrial&family=Didact+Gothic&family=Open+Sans:wght@600&display=swap">
<style>
  :root {
    --navy: #1b2a4e;
    --gold: #b59a5e;
    --ink-grey: #8d8f93;
    --text-grey: #9a9ca0;
    --paper: #ffffff;
  }
  * { margin: 0; padding: 0; box-sizing: border-box; }
  html, body { width: 908px; height: 1200px; overflow: hidden; background: var(--paper); }
  .letterhead { position: relative; width: 908px; height: 1200px; background: var(--paper); overflow: hidden; }

  .brand { position: absolute; left: 27px; top: 44px; }
  .brand-name { font-family: "Montserrat", sans-serif; font-weight: 600; font-size: 29px; letter-spacing: -0.5px; color: var(--navy); line-height: 1; }
  .brand-desc { font-family: "Montserrat", sans-serif; font-weight: 600; font-size: 6.5px; letter-spacing: 0.2px; color: var(--gold); margin-top: 3px; }

  .header-rule { position: absolute; left: 0; top: 101px; width: 703px; height: 1.5px; background: var(--gold); }

  .contact-list { position: absolute; left: 709px; top: 48px; list-style: none; font-family: "Questrial", sans-serif; font-size: 13px; color: var(--ink-grey); }
  .contact-list li { display: flex; align-items: center; gap: 4px; height: 18px; margin-bottom: 4px; }
  .contact-list svg { width: 11px; height: 11px; flex: none; }

  .recipient { position: absolute; left: 41px; top: 236px; font-family: "Questrial", sans-serif; color: var(--ink-grey); }
  .recipient-name { font-family: "Montserrat", sans-serif; font-weight: 700; font-size: 26px; letter-spacing: 0.3px; color: var(--ink-grey); margin-bottom: 6px; }
  .recipient p { font-size: 15px; line-height: 17px; margin-bottom: 10px; }
  .recipient .address { margin-bottom: 0; line-height: 20px; }

  .letter-date { position: absolute; right: 43px; top: 346px; font-family: "Open Sans", sans-serif; font-weight: 600; font-size: 16px; color: var(--ink-grey); }

  .letter-body { position: absolute; left: 36px; width: 829px; font-family: "Didact Gothic", sans-serif; font-size: 14.6px; line-height: 19.6px; color: var(--text-grey); text-align: justify; hyphens: auto; }
  .body-one { top: 405px; }
  .body-two { top: 543px; }
  .body-three { top: 681px; }

  .signer-title { position: absolute; left: 66px; top: 804px; font-family: "Didact Gothic", sans-serif; font-size: 21px; color: var(--ink-grey); }
  .signature { position: absolute; left: 86px; top: 850px; width: 165px; height: 96px; background: linear-gradient(135deg, #f1f1f2, #e4e4e6); border-radius: 4px; }

  .footer-band { position: absolute; left: 0; bottom: 0; width: 908px; height: 6px; background: var(--navy); }
</style>
</head>
<body>
<main class="letterhead">
  <header>
    <div class="brand">
      <div class="brand-name">VITARIDGE</div>
      <div class="brand-desc">COMMUNITY HEALTH CENTER</div>
    </div>
    <div class="header-rule"></div>
    <ul class="contact-list">
      <li>
        <svg viewBox="0 0 12 12" aria-hidden="true"><circle cx="6" cy="6" r="6" fill="#1b2a4e"/><path d="M4 3.2l1 1.2-.5.7c.4.9 1 1.5 1.9 1.9l.7-.5 1.2 1-.6.9c-2.3-.3-4.2-2.2-4.5-4.5z" fill="#fff"/></svg>
        0123-456-789
      </li>
      <li>
        <svg viewBox="0 0 12 12" aria-hidden="true"><circle cx="6" cy="6" r="6" fill="#1b2a4e"/><rect x="3" y="4" width="6" height="4" fill="none" stroke="#fff" stroke-width=".8"/><path d="M3 4l3 2.2L9 4" fill="none" stroke="#fff" stroke-width=".8"/></svg>
        info@vitaridgehealth.org
      </li>
      <li>
        <svg viewBox="0 0 12 12" aria-hidden="true"><circle cx="6" cy="6" r="6" fill="#1b2a4e"/><circle cx="6" cy="6" r="3.2" fill="none" stroke="#fff" stroke-width=".7"/><ellipse cx="6" cy="6" rx="1.4" ry="3.2" fill="none" stroke="#fff" stroke-width=".7"/><path d="M2.8 6h6.4" stroke="#fff" stroke-width=".7"/></svg>
        www.vitaridgehealth.org
      </li>
    </ul>
  </header>

  <section class="recipient">
    <h1 class="recipient-name">JANE MORROW</h1>
    <p>0123-456-789</p>
    <p>jane@morrowpatientcare.com</p>
    <p class="address">1234 City Your Ln. Suite<br>123 Dallas, TX 0000</p>
  </section>

  <p class="letter-date">12 December, 2023</p>

  <p class="letter-body body-one">Lorem ipsum dolor sit amet, consectetuer adipiscing elit, sed diam nonummy nibh euismod tincidunt ut laoreet dolore magna aliquam erat volutpat. Ut wisi enim ad minim veniam, quis nostrud exerci tation ullamcorper suscipit lobortis nisl ut aliquip ex ea commodo consequat. Duis autem vel eum iriure dolor in hendrerit in vulputate velit esse molestie consequat, vel illum dolore eu feugiat nulla facilisis at vero eros et accumsan et iusto odio dignissim qui blandit praesent luptatum zzril delenit augue duis dolore te feugait nulla facilisi.</p>

  <p class="letter-body body-two">Lorem ipsum dolor sit amet, cons ectetuer adipiscing elit, sed diam nonummy nibh euismod tincidunt ut laoreet dolore magna aliquam erat volutpat. Ut wisi enim ad minim veniam, quis nostrud exerci tation ullamcorper suscipit lobortis nisl ut aliquip ex ea commodo consequat.<br>Lorem ipsum dolor sit amet, consectetuer adipiscing elit, sed diam nonummy nibh euismod tincidunt ut laoreet dolore magna aliquam erat</p>

  <p class="letter-body body-three">Lorem ipsum dolor sit amet, cons ectetuer adipiscing elit, sed diam nonummy nibh euismod tincidunt ut laoreet dolore magna aliquam erat volutpat. Ut wisi enim ad minim veniam, quis nostrud exerci tation ullamcorper suscipit lobortis nisl ut aliquip ex ea commodo consequat. Lorem ipsum dolor sit zamet, consectetuer adipiscing elit, sed diam nonummy nibh euismod tincidunt.</p>

  <p class="signer-title">Managing Director</p>
  <div class="signature" role="img" aria-label="Handwritten signature of the managing director"></div>

  <div class="footer-band"></div>
</main>
</body>
</html>
```